Online Games Mobile Website Design

Important information:<br/>Style:<br/>- minimalistic flat<br/>- attention to the elements<br/>- The background is everywhere white, except for header, menu and footer.<br/>- everything is flat, without shadows, roundings, bulges, gradients<br/>- free choice of colors<br/>- use bright colors for contrasts<br/>- for a specific page, it is important to save every pixel in height (no need to make pointlessly large indents where they are not needed)<br/><br/>Fonts (recommended, but not required):<br/>for titles (red in layout) - Google sans<br/>for the rest of the text - Roboto<br/><br/>Features:<br/>All pictures of games (pictures with previews of games) should be with an aspect ratio of 16: 9, no others, this should immediately be taken into account.<br/><br/>Additionally, you need to make a logo redesign that will suit the new design.<br/><br/><br/>Specifically about the page to be redesigned - Page of the game<br/>This page contains the game and a list of similar games.<br/><br/>Check attached image for the layout details.<br/><br/>The description of the game is shown by clicking on the name of the game under the game.<br/>For evaluation, you need to provide a page with an open / hidden description of the game.<br/>When the description of the game is disclosed, there are Tag 1, Tag 2, Tag 3 labels - these are the tags to which the game belongs (shooter, arcade, racing, etc.).<br/>You need to choose a set of icons for tags, then use them on these labels.<br/><br/>Under the game (portrait) is a list of similar games.<br/>You must provide 3 options for this list:<br/><br/>1. List items have a border and are separated by indentation.<br/>2. List items without a border are separated by a horizontal line.<br/>3. Items without a border are only separated by indentation<br/>for point 2 and 3, center the text (to the right of the game image) along the upper left edge, as in a relayed video on youtube<br/><br/>For the design layout use pictures, texts, game names from the website Vultaroo.com.

Hello, I've posted my project just today. Thanks in advance

Target Market(s)

Mobile online games

Logo Text

Vultaroo / Online games

Number of Pages Required

1 page

Font styles to use
Sans Serif

Colors

Designer to choose colors to be used in the design.

Requirements
Must have
• Check our current Game Page view and do something that really much much better - https://vultaroo.com/winter-otter-dash-177/

```html
<!DOCTYPE html>
<html lang="en">
<head>
<meta charset="utf-8">
<title>Vultaroo – Winter Otter Dash</title>
<link rel="stylesheet" href="https://fonts.googleapis.com/css2?family=Quicksand:wght@500;600;700&family=Roboto:wght@400;500&display=swap">
<style>
  :root {
    --navy: #1e2156;
    --red: #b90e22;
    --blue: #2a86d8;
    --grey-bg: #f4f4f4;
    --grey-line: #d9d9d9;
    --text-muted: #666a72;
    --white: #ffffff;
  }
  * { margin: 0; padding: 0; box-sizing: border-box; }
  html, body { width: 1200px; height: 4160px; overflow: hidden; background: var(--white); }
  body { font-family: "Quicksand", sans-serif; color: var(--navy); position: relative; }

  .site-header { height: 224px; display: flex; align-items: center; justify-content: space-between; padding: 0 48px; }
  .brand { display: flex; align-items: center; gap: 24px; }
  .brand-dot { width: 150px; height: 150px; border-radius: 50%; background: var(--red); }
  .brand-text { display: flex; flex-direction: column; line-height: 1; }
  .brand-name { font-size: 72px; font-weight: 700; color: var(--navy); }
  .brand-tag { font-size: 43px; font-weight: 600; color: var(--blue); margin-top: 12px; letter-spacing: 1px; }
  .menu-toggle { width: 152px; height: 152px; border: 5px solid var(--navy); border-radius: 50%; display: flex; align-items: center; justify-content: center; }

  .hero { position: relative; height: 883px; background: linear-gradient(180deg, #5f8f6e 0%, #dfe9ef 45%, #f4f6f8 80%, #4a3326 100%); }
  .hero-art { position: absolute; inset: 0; }
  .hero-panel { position: absolute; left: 115px; top: 133px; width: 970px; height: 355px; background: rgba(30, 33, 60, 0.78); text-align: center; color: var(--white); padding-top: 38px; }
  .hero-title { font-size: 59px; font-weight: 700; }
  .hero-sub { font-size: 51px; font-weight: 500; margin-top: 14px; }
  .play-btn { display: inline-block; margin-top: 32px; background: var(--red); color: var(--white); font-size: 40px; font-weight: 700; padding: 14px 34px; border-radius: 8px; }

  .game-bar { height: 168px; background: var(--grey-bg); border-bottom: 3px solid var(--grey-line); display: flex; align-items: center; justify-content: space-between; padding: 0 48px; font-size: 51px; font-weight: 600; }
  .game-bar .name { color: var(--red); }
  .game-bar .plays { color: var(--navy); }

  .content { padding: 61px 48px 0; }
  .ad-banner { height: 136px; margin-bottom: 59px; }
  .ad-banner.dark { background: linear-gradient(90deg, #1a1c22, #2a2d36 70%, #e0641e); }
  .ad-banner.orange { background: linear-gradient(90deg, #f3a51c, #f07c12); }

  .game-card { height: 434px; border: 3px solid var(--grey-line); border-radius: 8px; background: var(--grey-bg); display: flex; padding: 24px 18px; margin-bottom: 64px; }
  .game-thumb { width: 480px; height: 384px; border-radius: 8px; flex: none; }
  .thumb-space { background: linear-gradient(180deg, #6a1f12, #c2461e 70%, #e08a3a); }
  .thumb-sea { background: linear-gradient(180deg, #1a8fd6, #47b8ec); }
  .thumb-taxi { background: linear-gradient(90deg, #4a5cf0 45%, #f2c418); }
  .thumb-pool { background: linear-gradient(180deg, #1e9a44, #33b85a); }
  .game-info { padding: 38px 0 0 53px; }
  .game-title { font-size: 53px; font-weight: 600; color: var(--blue); }
  .game-desc { font-family: "Roboto", sans-serif; font-size: 37px; line-height: 1.45; color: var(--text-muted); margin-top: 22px; }
  .game-plays { display: flex; align-items: center; gap: 16px; font-size: 43px; font-weight: 600; margin-top: 34px; }
  .game-plays.hot { color: var(--red); }
  .game-plays.cool { color: var(--navy); }

  .nav-bar { position: absolute; left: 0; top: 3795px; width: 1200px; height: 184px; background: var(--red); display: flex; align-items: center; justify-content: center; }
  .site-footer { position: absolute; left: 0; top: 3979px; width: 1200px; height: 181px; background: var(--navy); color: var(--white); display: flex; align-items: center; justify-content: space-between; padding: 0 53px 0 51px; font-size: 43px; font-weight: 600; }
</style>
</head>
<body>
  <header class="site-header">
    <div class="brand">
      <span class="brand-dot"></span>
      <div class="brand-text">
        <span class="brand-name">VULTAROO</span>
        <span class="brand-tag">ONLINE GAMES</span>
      </div>
    </div>
    <div class="menu-toggle">
      <svg width="40" height="34" viewBox="0 0 40 34"><g fill="#1e2156"><rect width="40" height="7" rx="2"/><rect y="13" width="40" height="7" rx="2"/><rect y="27" width="40" height="7" rx="2"/></g></svg>
    </div>
  </header>

  <section class="hero">
    <div class="hero-art" role="img" aria-label="Winter game scene with snowy pine trees, a decorated tree, coins and a small house"></div>
    <div class="hero-panel">
      <h1 class="hero-title">Winter Otter Dash</h1>
      <p class="hero-sub">The free game Winter Otter Dash</p>
      <span class="play-btn">Play Now</span>
    </div>
  </section>

  <div class="game-bar">
    <span class="name">Game 2</span>
    <span class="plays">10,687,511 Plays</span>
  </div>

  <main class="content">
    <div class="ad-banner dark" role="img" aria-label="Advertising banner for a new games site"></div>

    <article class="game-card">
      <div class="game-thumb thumb-space" role="img" aria-label="Game preview: runner on a red planet"></div>
      <div class="game-info">
        <h2 class="game-title">Game 2</h2>
        <p class="game-desc">Sed ut perspiciatis unde omn is<br>iste natus error sit volupta...</p>
        <p class="game-plays hot"><svg width="56" height="32" viewBox="0 0 56 32"><rect width="56" height="32" rx="16" fill="currentColor"/><rect x="11" y="14" width="14" height="4" fill="#f4f4f4"/><rect x="16" y="9" width="4" height="14" fill="#f4f4f4"/><circle cx="38" cy="12" r="3" fill="#f4f4f4"/><circle cx="44" cy="19" r="3" fill="#f4f4f4"/></svg>10,687,511 Plays</p>
      </div>
    </article>

    <article class="game-card">
      <div class="game-thumb thumb-sea" role="img" aria-label="Game preview: underwater scene"></div>
      <div class="game-info">
        <h2 class="game-title">Game 2</h2>
        <p class="game-desc">Sed ut perspiciatis unde omn is<br>iste natus error sit volupta...</p>
        <p class="game-plays hot"><svg width="56" height="32" viewBox="0 0 56 32"><rect width="56" height="32" rx="16" fill="currentColor"/><rect x="11" y="14" width="14" height="4" fill="#f4f4f4"/><rect x="16" y="9" width="4" height="14" fill="#f4f4f4"/><circle cx="38" cy="12" r="3" fill="#f4f4f4"/><circle cx="44" cy="19" r="3" fill="#f4f4f4"/></svg>10,687,511 Plays</p>
      </div>
    </article>

    <div class="ad-banner orange" role="img" aria-label="Advertising banner for a fruit matching game download"></div>

    <article class="game-card">
      <div class="game-thumb thumb-taxi" role="img" aria-label="Game preview: yellow taxi on a blue background"></div>
      <div class="game-info">
        <h2 class="game-title">Game 2</h2>
        <p class="game-desc">Sed ut perspiciatis unde omn is<br>iste natus error sit volupta...</p>
        <p class="game-plays cool"><svg width="56" height="32" viewBox="0 0 56 32"><rect width="56" height="32" rx="16" fill="currentColor"/><rect x="11" y="14" width="14" height="4" fill="#f4f4f4"/><rect x="16" y="9" width="4" height="14" fill="#f4f4f4"/><circle cx="38" cy="12" r="3" fill="#f4f4f4"/><circle cx="44" cy="19" r="3" fill="#f4f4f4"/></svg>10,687,511 Plays</p>
      </div>
    </article>

    <article class="game-card">
      <div class="game-thumb thumb-pool" role="img" aria-label="Game preview: billiard balls and cue on green felt"></div>
      <div class="game-info">
        <h2 class="game-title">Game 2</h2>
        <p class="game-desc">Sed ut perspiciatis unde omn is<br>iste natus error sit volupta...</p>
        <p class="game-plays cool"><svg width="56" height="32" viewBox="0 0 56 32"><rect width="56" height="32" rx="16" fill="currentColor"/><rect x="11" y="14" width="14" height="4" fill="#f4f4f4"/><rect x="16" y="9" width="4" height="14" fill="#f4f4f4"/><circle cx="38" cy="12" r="3" fill="#f4f4f4"/><circle cx="44" cy="19" r="3" fill="#f4f4f4"/></svg>10,687,511 Plays</p>
      </div>
    </article>
  </main>

  <nav class="nav-bar">
    <svg width="72" height="60" viewBox="0 0 72 60"><g fill="#ffffff"><rect width="72" height="11" rx="2"/><rect y="24" width="72" height="11" rx="2"/><rect y="49" width="72" height="11" rx="2"/></g></svg>
  </nav>

  <footer class="site-footer">
    <span>Copyright 2020</span>
    <span>Affiliate Program</span>
  </footer>
</body>
</html>
```